Restyle corporate identity (+ logo) for a road construction company

We need a new logo and stationary design for our company VARNOK path. VARNOK path® increases the road base strength, while reducing major costs and time of road construction. Attached some examples of the current design.

Our wishes for the new logo:
- Business look
- Style sheet
- Modern

More information: www.varnokpath.example
Updates

Target Market(s)

Government

Industry/Entity Type

Construction

Requirements
Must have
• Logo (with road sign) + text

```html
<!DOCTYPE html>
<html lang="en">
<head>
<meta charset="utf-8">
<title>VARNOK path – Business Card</title>
<link rel="stylesheet" href="https://fonts.googleapis.com/css2?family=Open+Sans:wght@400;600&display=swap">
<style>
  :root {
    --backdrop: #9b9b9b;
    --card-light: #f1f1f0;
    --brand-blue: #0b7be0;
    --text-dark: #4a4a4a;
    --text-muted: #8a8a8a;
    --divider: #9c9c9c;
    --white: #ffffff;
  }
  * { margin: 0; padding: 0; box-sizing: border-box; }
  html, body {
    width: 1105px;
    height: 1200px;
    overflow: hidden;
    background: var(--backdrop);
    font-family: "Open Sans", sans-serif;
  }
  .stage { position: relative; width: 1105px; height: 1200px; }

  .card {
    position: absolute;
    left: 180px;
    width: 745px;
    height: 425px;
  }
  .card--front { top: 120px; background: var(--card-light); }
  .card--back  { top: 640px; background: var(--brand-blue); }

  .brand-name {
    position: absolute;
    left: 0; right: 0;
    top: 88px;
    text-align: center;
    font-size: 54px;
    font-weight: 600;
    letter-spacing: 2px;
    color: var(--brand-blue);
  }

  .person {
    position: absolute;
    right: 432px;
    top: 256px;
    text-align: right;
  }
  .person__name {
    font-size: 27px;
    font-weight: 600;
    color: var(--brand-blue);
    line-height: 1.2;
  }
  .person__role {
    font-size: 19px;
    color: var(--text-muted);
    line-height: 1.3;
  }

  .divider {
    position: absolute;
    left: 333px;
    top: 200px;
    width: 1px;
    height: 173px;
    background: var(--divider);
  }

  .address {
    position: absolute;
    left: 356px;
    top: 199px;
    font-size: 19px;
    line-height: 26px;
    color: var(--text-dark);
    font-style: normal;
  }

  .contact-list {
    position: absolute;
    left: 360px;
    top: 287px;
    list-style: none;
  }
  .contact-list__item {
    display: flex;
    align-items: center;
    height: 28px;
    font-size: 19px;
    color: var(--text-dark);
  }
  .contact-list__icon {
    width: 16px;
    height: 16px;
    margin-right: 12px;
    fill: var(--brand-blue);
    flex-shrink: 0;
  }

  .brand-name--reverse {
    top: 150px;
    font-size: 64px;
    color: var(--white);
  }
  .back-url {
    position: absolute;
    left: 0; right: 0;
    top: 357px;
    text-align: center;
    font-size: 20px;
    letter-spacing: 7px;
    color: var(--white);
  }
</style>
</head>
<body>
<main class="stage">

  <section class="card card--front">
    <div class="brand-name">VARNOK path</div>

    <div class="person">
      <p class="person__name">Maren Holt</p>
      <p class="person__role">CEO/Founder</p>
    </div>

    <div class="divider"></div>

    <address class="address">
      Lindenkade 58<br>
      3011 BK Westerhaven<br>
      The Netherlands
    </address>

    <ul class="contact-list">
      <li class="contact-list__item">
        <svg class="contact-list__icon" viewBox="0 0 16 16" aria-hidden="true">
          <path d="M3.2 1c.4 0 .7.2.9.5l1.6 2.6c.2.4.1.9-.2 1.2L4.4 6.4c.9 2 2.5 3.6 4.6 4.6l1.1-1.1c.3-.3.8-.4 1.2-.2l2.6 1.6c.3.2.5.6.5.9v2.1c0 .6-.5 1.1-1.1 1.1C6.6 15.4.6 9.4.6 2.1.6 1.5 1.1 1 1.7 1z"/>
        </svg>
        612 408 3917
      </li>
      <li class="contact-list__item">
        <svg class="contact-list__icon" viewBox="0 0 16 16" aria-hidden="true">
          <path d="M1 3.5h14v9H1z M2 4.5l6 4.2 6-4.2v-.2H2z" fill-rule="evenodd"/>
        </svg>
        mail@varnokpath.example
      </li>
      <li class="contact-list__item">
        <svg class="contact-list__icon" viewBox="0 0 16 16" aria-hidden="true">
          <circle cx="8" cy="8" r="7.2"/>
          <path d="M5 3.5c1.2.4 1.6 1.5 1 2.4-.6.8-1.8.6-2 1.8-.1.9.9 1.4.8 2.5M10.5 2.6c-.6 1.1.3 2 1.2 2.1.9.1 1.7.9 1.2 2-.5 1-1.6.8-2 1.9-.3.9.4 2-.5 3.2" fill="none" stroke="var(--card-light)" stroke-width="1.1"/>
        </svg>
        www.varnokpath.example
      </li>
    </ul>
  </section>

  <section class="card card--back">
    <div class="brand-name brand-name--reverse">VARNOK path</div>
    <p class="back-url">www.varnokpath.example</p>
  </section>

</main>
</body>
</html>
```